Tellmora Corporate Stationery

Look for design of all new corporate stationery for an existing insurance broking business that is going through a redesign and move from older partners to younger family members. New Logo is attached. Company is Brisbane based.
Colours in the Logo is Hex #43bed8 and website features a lot of hex #17b8d8. Website front page "A plan to protect you" - headline. "Professional and Individual advice to protect your greatest assets" - tagline.

Stationery required: Business Cards, Letter head, Thank-you cards, Birthday cards, Presentation folders, With Compliment slips and a powerpoint template. We also would like to send a card to all customers with the something along of the lines of "something new".

Target Market(s)

Customers of Insurance business looking at superannuation, life and income protection insurance, investment advice and wills

Industry/Entity Type

Insurance Broker

Font styles to use
Other font styles liked:
• same as logo

Requirements
Must have
• The above designs for new stationery for the new business including:
• Business Cards, Letter head, Thank-you cards, Birthday cards, Presentation folders, With Compliment slips and a powerpoint template. We also would like to send a card to all customers with the something along of the lines of "something new".
Nice to have
• It is a new look - long time family business being passed to next generation - big focus on advice for YOU, individual advice etc..

```html
<!DOCTYPE html>
<html lang="en">
<head>
<meta charset="utf-8">
<title>Tellmora Presentation Template Sets</title>
<link rel="stylesheet" href="https://fonts.googleapis.com/css2?family=Open+Sans:wght@400;600;700&display=swap">
<style>
  :root {
    --board: #1c1c1e;
    --cyan: #3dbdd8;
    --cyan-soft: #c9ebf3;
    --cyan-pale: #e9f6f9;
    --teal: #1d6e80;
    --teal-mid: #1f8aa0;
    --grey: #77787b;
    --ink: #6b6b6b;
    --white: #ffffff;
  }
  html, body {
    margin: 0;
    width: 1200px;
    height: 1200px;
    overflow: hidden;
    background: var(--board);
    font-family: "Open Sans", sans-serif;
  }
  .board { position: relative; width: 1200px; height: 1200px; }
  .set-label {
    position: absolute;
    margin: 0;
    color: var(--white);
    font-weight: 400;
    font-size: 38px;
    line-height: 1;
  }
  .slide {
    position: absolute;
    width: 548px;
    height: 410px;
    display: block;
  }
  .slide text { font-family: "Open Sans", sans-serif; }
  .brand { fill: var(--cyan); font-weight: 600; }
  .headline { font-weight: 700; }
  .body-copy { fill: var(--ink); font-size: 9px; }
  .legal { font-size: 8px; }
</style>
</head>
<body>
<main class="board">

  <h2 class="set-label" style="left:70px;top:82px">Set _ 1</h2>
  <h2 class="set-label" style="left:645px;top:82px">Set _ 2</h2>
  <h2 class="set-label" style="left:70px;top:644px">Set _ 3</h2>
  <h2 class="set-label" style="left:645px;top:644px">Set _ 4</h2>

  <!-- Welcome slide -->
  <svg class="slide" style="left:32px;top:145px" viewBox="0 0 685 512" aria-label="Welcome slide">
    <defs>
      <linearGradient id="welcome-sky" x1="0" y1="0" x2="0" y2="1">
        <stop offset="0" stop-color="#ffffff"/>
        <stop offset="0.25" stop-color="#ffffff"/>
        <stop offset="1" stop-color="#a9dfec"/>
      </linearGradient>
    </defs>
    <rect width="685" height="512" fill="url(#welcome-sky)"/>
    <path d="M0 340 C120 300 200 275 300 300 C400 325 460 380 560 350 C620 330 660 300 685 295 L685 512 L0 512 Z" fill="var(--cyan)"/>
    <path d="M0 338 C120 298 200 273 300 298 C400 323 460 378 560 348 C620 328 660 298 685 293" fill="none" stroke="#ffffff" stroke-width="5"/>
    <path d="M0 322 C120 285 200 270 300 292 C400 315 460 368 560 340 C620 322 660 298 685 288" fill="none" stroke="var(--grey)" stroke-width="5"/>
    <text class="headline" x="615" y="105" text-anchor="end" font-size="60" fill="var(--cyan)">WELCOME</text>
    <text class="brand" x="470" y="252" text-anchor="middle" font-size="30">TELLMORA</text>
    <text class="brand" x="470" y="276" text-anchor="middle" font-size="15">FINANCIAL GROUP</text>
    <text class="headline" x="658" y="422" text-anchor="end" font-size="32" fill="var(--white)">A PLAN TO PROTECT YOU</text>
    <text x="650" y="447" text-anchor="end" font-size="14" fill="var(--white)">Professional &amp; Individual advice to protect your greatest assets</text>
    <text class="legal" x="663" y="490" text-anchor="end" font-size="7" fill="var(--white)">Authorised Representatives of Veranta AFS Licence No 518204</text>
  </svg>

  <!-- Welcome content slide -->
  <svg class="slide" style="left:614px;top:142px" viewBox="0 0 687 514" aria-label="Introduction slide">
    <defs>
      <linearGradient id="intro-header" x1="0" y1="0" x2="0" y2="1">
        <stop offset="0" stop-color="#d7f0f6"/>
        <stop offset="1" stop-color="#eef9fb"/>
      </linearGradient>
      <linearGradient id="intro-foot" x1="0" y1="0" x2="0" y2="1">
        <stop offset="0" stop-color="#ffffff"/>
        <stop offset="1" stop-color="#d9f0f6"/>
      </linearGradient>
    </defs>
    <rect width="687" height="514" fill="var(--cyan-pale)"/>
    <rect width="687" height="102" fill="url(#intro-header)"/>
    <rect y="370" width="687" height="144" fill="url(#intro-foot)"/>
    <text class="headline" x="25" y="57" font-size="31" fill="var(--teal-mid)">A PLAN TO PROTECT YOU</text>
    <text x="470" y="76" text-anchor="end" font-size="11" fill="var(--ink)">Professional &amp; Individual advice to protect your greatest assets</text>
    <text class="body-copy" x="18" y="121">Lorem Ipsum has been the industry's standard dummy text ever since the 1500s, when an unknown</text>
    <text class="body-copy" x="18" y="138">printer took a galley of type and scrambled it to make a type specimen book. It has survived not only five</text>
    <text class="body-copy" x="18" y="155">centuries, but also the leap into electronic typesetting, remaining essentially unchanged.</text>
    <text class="brand" x="544" y="262" text-anchor="middle" font-size="26">TELLMORA</text>
    <text class="brand" x="544" y="280" text-anchor="middle" font-size="13">FINANCIAL GROUP</text>
    <text x="386" y="345" text-anchor="middle" font-size="38" fill="var(--cyan)">Welcome</text>
    <path d="M200 356 L472 356 L478 364 L478 374 L200 374 Z" fill="var(--grey)"/>
    <line x1="200" y1="379" x2="558" y2="379" stroke="var(--cyan)" stroke-width="1.5"/>
    <polyline points="0,424 74,424 74,377 177,377" fill="none" stroke="var(--cyan)" stroke-width="1"/>
    <circle cx="177" cy="377" r="5" fill="var(--cyan)"/>
    <text class="brand" x="390" y="430" text-anchor="middle" font-size="44">TELLMORA</text>
    <text class="brand" x="390" y="456" text-anchor="middle" font-size="22">FINANCIAL GROUP</text>
    <text class="legal" x="645" y="497" text-anchor="end" font-size="9" fill="#333">Authorised Representatives of Veranta AFS Licence No 518204</text>
  </svg>

  <!-- Growth slide -->
  <svg class="slide" style="left:32px;top:706px" viewBox="0 0 685 512" aria-label="Growth slide">
    <defs>
      <linearGradient id="growth-sky" x1="0" y1="0" x2="1" y2="1">
        <stop offset="0" stop-color="#e6f5f9"/>
        <stop offset="1" stop-color="#9fd9e8"/>
      </linearGradient>
      <linearGradient id="growth-art" x1="0" y1="1" x2="1" y2="0">
        <stop offset="0" stop-color="#7ccfe2"/>
        <stop offset="0.5" stop-color="#d8f0f6"/>
        <stop offset="1" stop-color="#4cc2dc"/>
      </linearGradient>
    </defs>
    <rect width="685" height="512" fill="url(#growth-sky)"/>
    <rect x="0" y="272" width="685" height="200" fill="url(#growth-art)" role="img" aria-label="Illustration of a rising zigzag growth arrow in cyan and teal"/>
    <text class="headline" x="36" y="65" font-size="39" fill="var(--teal)">A PLAN TO PROTECT YOU</text>
    <text x="78" y="90" font-size="15" fill="var(--teal-mid)">Professional &amp; Individual advice to protect your greatest assets</text>
    <text class="body-copy" x="29" y="132">Lorem Ipsum has been the industry's standard dummy text ever since the 1500s, when an unknown</text>
    <text class="body-copy" x="29" y="149">printer took a galley of type and scrambled it to make a type specimen book. It has survived not only five</text>
    <text class="body-copy" x="29" y="166">centuries, but also the leap into electronic typesetting, remaining essentially unchanged.</text>
    <text class="body-copy" x="29" y="190">Lorem Ipsum has been the industry's standard dummy</text>
    <text class="body-copy" x="29" y="207">text ever since the 1500s, when an unknown printer</text>
    <text class="body-copy" x="29" y="224">took a galley of type and scrambled it to make a type</text>
    <text class="body-copy" x="29" y="241">specimen book. It has survived not only five centuries,</text>
    <text class="body-copy" x="29" y="258">but also the leap into electronic typesetting, remaining</text>
    <text class="brand" x="520" y="434" text-anchor="middle" font-size="28">TELLMORA</text>
    <text class="brand" x="520" y="453" text-anchor="middle" font-size="14">FINANCIAL GROUP</text>
    <polygon points="14,472 685,472 685,502 6,502" fill="var(--teal)"/>
    <text class="legal" x="654" y="492" text-anchor="end" font-size="9" fill="var(--white)">Authorised Representatives of Veranta AFS Licence No 518204</text>
  </svg>

  <!-- Advice slide -->
  <svg class="slide" style="left:614px;top:704px" viewBox="0 0 689 515" aria-label="Advice slide">
    <defs>
      <linearGradient id="figure-tone" x1="0" y1="0" x2="1" y2="1">
        <stop offset="0" stop-color="#f3f3f3"/>
        <stop offset="0.5" stop-color="#f4f1b8"/>
        <stop offset="1" stop-color="#e6e6e6"/>
      </linearGradient>
    </defs>
    <rect width="689" height="515" fill="var(--white)"/>
    <path d="M340 0 L689 0 L689 108 C600 100 470 70 340 0 Z" fill="var(--cyan)"/>
    <path d="M370 35 C450 95 560 122 689 125" fill="none" stroke="var(--grey)" stroke-width="6"/>
    <path d="M395 55 C470 110 570 140 689 145" fill="none" stroke="var(--teal)" stroke-width="8"/>
    <text class="headline" x="35" y="84" font-size="40" fill="var(--teal)">A PLAN TO</text>
    <text class="headline" x="83" y="134" font-size="40" fill="var(--teal)">PROTECT YOU</text>
    <text x="30" y="153" font-size="12" fill="var(--teal-mid)">Professional &amp; Individual advice to protect your greatest assets</text>
    <text class="brand" x="200" y="210" text-anchor="middle" font-size="30">TELLMORA</text>
    <text class="brand" x="200" y="230" text-anchor="middle" font-size="15">FINANCIAL GROUP</text>
    <g text-anchor="middle">
      <text class="body-copy" x="200" y="275">Lorem Ipsum has been the industry's standard dummy text ever since the</text>
      <text class="body-copy" x="200" y="292">1500s, when an unknown printer took a galley of type and scrambled it to make</text>
      <text class="body-copy" x="200" y="309">a type specimen book. It has survived not only five centuries, but also the leap</text>
      <text class="body-copy" x="200" y="326">into electronic typesetting, remaining essentially unchanged.</text>
      <text class="body-copy" x="200" y="359">Lorem Ipsum has been the industry's standard dummy text ever since the</text>
      <text class="body-copy" x="200" y="376">1500s, when an unknown printer took a galley of type and scrambled it to make</text>
      <text class="body-copy" x="200" y="393">a type specimen book. It has survived not only five centuries, but also the leap</text>
      <text class="body-copy" x="200" y="410">into electronic typesetting, remaining essentially unchanged.</text>
    </g>
    <rect x="432" y="155" width="215" height="300" rx="6" fill="url(#figure-tone)" role="img" aria-label="Illustration of a 3D figure in a tie leaning on a large yellow dollar sign"/>
    <rect x="232" y="480" width="457" height="35" fill="var(--cyan)"/>
    <text x="460" y="502" text-anchor="middle" font-size="12" font-weight="700" fill="var(--white)" letter-spacing="0.5">Authorised Representatives of Veranta AFS Licence No 518204</text>
  </svg>

</main>
</body>
</html>
```